Business Card Design for Occupational Medicine Start Up Company

We need to design a professional business card. We are a healthcare company providing occupational medicine services to blue collar industries. We are professional, efficient and high quality service providers.

Target Market(s)

Blue Collar Industry: Shipbuilding, Ports, Trucking Companies; The Executives and Safety Officers for these companies

Industry/Entity Type

Healthcare

Contact Information for Business Card

Logo, Name, Title, Email, Phone

Other font styles liked:
• Please match our Brand Guide

Requirements
Must have
• Our Company Colors and Logo

```html
<!DOCTYPE html>
<html lang="en">
<head>
<meta charset="utf-8">
<title>Harborline Clinics – Business Card</title>
<link rel="stylesheet" href="https://fonts.googleapis.com/css2?family=Montserrat:wght@400;600&family=Hind:wght@400;600&display=swap">
<style>
  :root {
    --navy: #2e3a8c;
    --ink: #1a1a1a;
    --amber: #f5b352;
    --paper: #ffffff;
    --edge: #cfcfcf;
    --page: #ffffff;
  }
  * { margin: 0; padding: 0; box-sizing: border-box; }
  html, body { width: 1200px; height: 1200px; overflow: hidden; background: var(--page); }
  .sheet { position: relative; width: 1200px; height: 1200px; }
  .card { position: absolute; top: 452px; width: 517px; height: 295px; }
  .card--front { left: 63px; background: var(--paper); border: 1px solid var(--edge); }
  .card--back { left: 620px; background: var(--amber); }

  .brand { font-family: "Montserrat", sans-serif; font-weight: 600; color: var(--navy); text-align: center; line-height: 1; }
  .brand__dot { display: block; border-radius: 50%; background: var(--navy); }

  .card--front .brand { position: absolute; left: 336px; top: 50px; width: 150px; }
  .card--front .brand__name { font-size: 17px; letter-spacing: 0.2px; }
  .card--front .brand__sub { font-size: 10px; letter-spacing: 3.6px; margin-top: 3px; padding-left: 3px; }
  .card--front .brand__dot { position: absolute; left: -16px; top: 4px; width: 10px; height: 10px; }

  .person { position: absolute; left: 27px; top: 168px; font-family: "Hind", sans-serif; }
  .person__name { font-size: 34px; line-height: 1; color: var(--ink); font-weight: 400; }
  .person__name b { font-weight: 600; }
  .person__title { font-size: 16px; line-height: 1; color: var(--ink); margin-top: 1px; }
  .contact { list-style: none; margin-top: 14px; }
  .contact__item { display: flex; align-items: center; gap: 6px; font-size: 16px; line-height: 20px; color: var(--ink); }
  .contact__item b { font-weight: 600; }
  .contact__icon { width: 11px; height: 11px; flex: none; }

  .card--back .brand { position: absolute; left: 0; right: 0; top: 86px; }
  .card--back .brand__dot { width: 62px; height: 62px; margin: 0 auto 22px; }
  .card--back .brand__name { font-size: 31px; }
  .card--back .brand__sub { font-size: 17px; letter-spacing: 8px; margin-top: 4px; padding-left: 8px; }
</style>
</head>
<body>
<main class="sheet">
  <section class="card card--front" aria-label="Business card front">
    <div class="brand">
      <span class="brand__dot"></span>
      <div class="brand__name">HARBORLINE</div>
      <div class="brand__sub">CLINICS</div>
    </div>
    <div class="person">
      <h1 class="person__name"><b>Dana</b> Morrow</h1>
      <p class="person__title">Managing Director</p>
      <ul class="contact">
        <li class="contact__item">
          <svg class="contact__icon" viewBox="0 0 11 11" aria-hidden="true"><rect width="11" height="11" fill="#2e3a8c"/><rect x="2.5" y="3.2" width="6" height="4.6" fill="none" stroke="#fff" stroke-width="0.9"/><path d="M2.5 3.4 L5.5 5.8 L8.5 3.4" fill="none" stroke="#fff" stroke-width="0.9"/></svg>
          danamorrow@mailbox.com
        </li>
        <li class="contact__item">
          <svg class="contact__icon" viewBox="0 0 11 11" aria-hidden="true"><rect width="11" height="11" fill="#2e3a8c"/><path d="M3.2 2.4 L4.5 2.4 L5 4 L4.2 4.7 Q5 6.3 6.4 6.9 L7.1 6.1 L8.6 6.6 L8.6 7.9 Q8 8.6 7 8.5 Q3 7.7 2.5 3.3 Q2.6 2.6 3.2 2.4 Z" fill="#fff"/></svg>
          www.<b>harborline</b>.com
        </li>
      </ul>
    </div>
  </section>

  <section class="card card--back" aria-label="Business card back">
    <div class="brand">
      <span class="brand__dot"></span>
      <div class="brand__name">HARBORLINE</div>
      <div class="brand__sub">CLINICS</div>
    </div>
  </section>
</main>
</body>
</html>
```